Stylish Business Cards Wanted

- DOUBLE SIDED Design Required -

High end, edgy cards for a corporate and personal stylist. Must include logo,
Name: Belinda Harwick
Title: Director and Stylist
telephone : +61 8 7142 5809
email: belinda@theloombriefing.example
website: theloombriefing.example
Tag: Corporate Workwear & Uniform Specialist | Personal Stylist
Would like nice icons for telephone, email, website

Target Market(s)

Businesses wanting stylish uniforms, people wanting stylish wardrobes

Industry/Entity Type

Corporate Workwear Stylist

Contact Information for Business Card

I would like black, white and gold foiling incorporated in the design - possibly a touch of the other colours on my branding guide attached Name: Belinda Harwick Title: Director and Stylist telephone : +61 8 7142 5809 email: belinda@theloombriefing.example website: theloombriefing.example Tag: Corporate Workwear & Uniform Specialist | Personal Stylist Would like nice icons for telephone, email, website

Font styles to use
Other font styles liked:
• Raleway

Colors

Designer to choose colors to be used in the design.

Requirements
Must have
• Gold foil accents

```html
<!DOCTYPE html>
<html lang="en">
<head>
<meta charset="utf-8">
<title>The Loom Briefing — Business Cards</title>
<link rel="stylesheet" href="https://fonts.googleapis.com/css2?family=Raleway:wght@500;600;700&family=Montserrat:wght@500;600&family=Arimo&display=swap">
<style>
  :root {
    --backdrop: #dcdcdc;
    --ink: #0b0b0b;
    --paper: #ffffff;
    --gold: #e3be5c;
    --muted: #555555;
  }
  * { box-sizing: border-box; margin: 0; padding: 0; }
  html, body { width: 1200px; height: 900px; overflow: hidden; }
  body {
    background: var(--backdrop);
    position: relative;
  }
  .card {
    position: absolute;
    width: 620px;
    height: 354px;
    box-shadow: 0 6px 14px rgba(0,0,0,0.25);
    overflow: hidden;
  }

  /* Front */
  .card--front {
    left: 250px; top: 60px;
    background: var(--ink);
    display: flex; align-items: center; justify-content: center;
  }
  .brand-name {
    font-family: "Raleway", sans-serif;
    font-weight: 700;
    color: var(--gold);
    text-transform: uppercase;
    text-align: center;
    letter-spacing: 0.12em;
    line-height: 1.05;
  }
  .card--front .brand-name { font-size: 58px; }

  /* Back */
  .card--back {
    left: 330px; top: 470px;
    background: var(--paper);
  }
  .brand-block {
    position: absolute;
    left: 0; top: 0;
    width: 262px; height: 250px;
    display: flex; align-items: center; justify-content: center;
  }
  .card--back .brand-name {
    color: var(--ink);
    font-size: 30px;
  }
  .divider {
    position: absolute;
    left: 262px; top: 34px;
    width: 2px; height: 180px;
    background: var(--gold);
  }
  .contact {
    position: absolute;
    left: 300px; top: 50px;
    right: 20px;
  }
  .contact__name {
    font-family: "Raleway", sans-serif;
    font-weight: 600;
    font-size: 21px;
    color: var(--ink);
  }
  .contact__title {
    font-family: "Arimo", sans-serif;
    font-size: 11.5px;
    color: var(--muted);
    margin-top: 1px;
  }
  .contact__list { list-style: none; margin-top: 28px; }
  .contact__item {
    display: flex; align-items: center; gap: 14px;
    font-family: "Arimo", sans-serif;
    font-size: 13.5px;
    color: var(--ink);
    margin-bottom: 9px;
  }
  .contact__icon { width: 18px; height: 18px; flex: none; }
  .gold-rule {
    position: absolute;
    left: 0; right: 0; top: 250px;
    height: 3px;
    background: var(--gold);
  }
  .tagline-band {
    position: absolute;
    left: 0; right: 0; top: 260px; bottom: 0;
    background: var(--ink);
    display: flex; flex-direction: column; align-items: center; justify-content: center;
    font-family: "Montserrat", sans-serif;
    font-weight: 500;
    font-size: 18px;
    letter-spacing: 0.02em;
    color: var(--gold);
    text-transform: uppercase;
    line-height: 1.3;
  }
</style>
</head>
<body>

  <section class="card card--front" aria-label="Card front">
    <p class="brand-name">The Loom<br>Briefing</p>
  </section>

  <section class="card card--back" aria-label="Card back">
    <div class="brand-block">
      <p class="brand-name">The Loom<br>Briefing</p>
    </div>
    <div class="divider"></div>

    <div class="contact">
      <h1 class="contact__name">Belinda Harwick</h1>
      <p class="contact__title">Director and Stylist</p>
      <ul class="contact__list">
        <li class="contact__item">
          <svg class="contact__icon" viewBox="0 0 20 20" aria-hidden="true">
            <circle cx="10" cy="10" r="10" fill="#0b0b0b"/>
            <path d="M7 5.5l1.6 0 .8 2.4-1.1.8a6 6 0 0 0 3 3l.8-1.1 2.4.8v1.6a1 1 0 0 1-1 1A8 8 0 0 1 6 6.5a1 1 0 0 1 1-1z" fill="#e3be5c"/>
          </svg>
          <span>+61 8 7142 5809</span>
        </li>
        <li class="contact__item">
          <svg class="contact__icon" viewBox="0 0 20 20" aria-hidden="true">
            <circle cx="10" cy="10" r="10" fill="#0b0b0b"/>
            <rect x="5" y="6.5" width="10" height="7" fill="none" stroke="#e3be5c" stroke-width="1.2"/>
            <path d="M5 6.5l5 4 5-4" fill="none" stroke="#e3be5c" stroke-width="1.2"/>
          </svg>
          <span>belinda@theloombriefing.example</span>
        </li>
        <li class="contact__item">
          <svg class="contact__icon" viewBox="0 0 20 20" aria-hidden="true">
            <circle cx="10" cy="10" r="10" fill="#0b0b0b"/>
            <circle cx="10" cy="10" r="5" fill="none" stroke="#e3be5c" stroke-width="1.1"/>
            <ellipse cx="10" cy="10" rx="2.2" ry="5" fill="none" stroke="#e3be5c" stroke-width="1"/>
            <path d="M5 10h10" stroke="#e3be5c" stroke-width="1"/>
          </svg>
          <span>theloombriefing.example</span>
        </li>
      </ul>
    </div>

    <div class="gold-rule"></div>
    <div class="tagline-band">
      <span>Corporate Workwear</span>
      <span>Uniform Specialist &nbsp;|&nbsp; Personal Stylist</span>
    </div>
  </section>

</body>
</html>
```